Box Package Design for a brand new patented shower head

We need a box packaging design and a design for a manual(insert) that goes inside the box. This is for a brand new patented shower head soon to be launched. We have been in the tapware business for over 25 years, always providing best quality innovative products, the "only-one-of-its-kind" in the market.
We already have all the contents, images, and specific design instructions ready. We have uploaded the 2 files regarding the design instructions (one for the box, and one for the manual).
Because of the file size, related files you need to work on can be downloaded through the following Cargoshelf links
Box design:
https://www.cargoshelf-files.net/s/tkvrpwm2zq8hdn/Box_design.zip?dl=0
Manual design:
https://www.cargoshelf-files.net/s/wvn4rkpa7tmq2x/Manual_design.zip?dl=0
Updates
Reason: We would like to have more time to receive designs and communicate with the designers.
Thank you for your interest in this project.
We have extended deadline to receive more designs and to communicate.
Also we have guaranteed the payment :) Looking forward to your great designs!
Reason: Needed more time for changes and communication with designers.
Target Market(s)
Customers interested in bathroom/shower/tap upgrades, DIY home renovations
Requirements
Must have
- Please include all the design instructions we have specified in the PPT files.
Nice to have
- It would be great to see some creative layouts using our current images.

```html
<!DOCTYPE html>
<html lang="en">
<head>
<meta charset="utf-8">
<title>Shower Head Manual</title>
<link href="https://fonts.googleapis.com/css2?family=Kaushan+Script&family=Roboto+Condensed:wght@300;400&display=swap" rel="stylesheet">
<style>
:root{
  --sky-top:#1f73c9;
  --sky-mid:#4aa3e6;
  --sky-low:#bfe6f7;
  --panel-blue:#0a7ad4;
  --panel-blue-deep:#0666b8;
  --navy:#0b2d4e;
  --card-navy:#0d2f4f;
  --white:#ffffff;
  --ink:#1c1c1c;
  --grey-text:#ebebeb;
  --wood:#b89a72;
  --wood-dark:#9d7f58;
}
*{box-sizing:border-box;margin:0;padding:0}
html,body{width:1200px;height:848px;overflow:hidden}
body{
  position:relative;
  font-family:"Roboto Condensed",Arial,sans-serif;
  background:linear-gradient(180deg,var(--sky-top) 0%,var(--sky-mid) 45%,var(--sky-low) 100%);
}
.sheet{position:absolute;inset:0}
.banner{
  position:absolute;height:42px;white-space:nowrap;overflow:hidden;
  background:linear-gradient(90deg,rgba(11,45,78,0) 0%,var(--navy) 18%,var(--navy) 82%,rgba(11,45,78,0) 100%);
  color:var(--white);font-family:"Kaushan Script",cursive;font-size:27px;
  display:flex;align-items:center;justify-content:center;letter-spacing:.3px;
}
.banner-assembly{left:392px;top:24px;width:384px;height:44px;font-size:21px}
.parts-panel{
  position:absolute;left:40px;top:60px;width:314px;height:370px;
  background:var(--white);border-radius:8px;overflow:hidden;
}
.parts-drawing{position:absolute;left:92px;top:10px;width:130px;height:350px;border-radius:6px;background:linear-gradient(180deg,#f4f4f4,#e2e2e2)}
.part-label{position:absolute;font-size:7.5px;color:#333;line-height:1.2}
.install-panel{
  position:absolute;left:14px;top:486px;width:364px;height:356px;
  background:var(--grey-text);
}
.install-icons{position:absolute;left:0;top:0;width:116px;height:100%;background:var(--white)}
.install-row{
  position:absolute;left:116px;width:248px;height:71px;
  display:flex;align-items:center;justify-content:center;text-align:center;
  font-size:10.4px;line-height:1.25;color:var(--ink);padding:0 6px 0 10px;
}
.install-row::before{
  content:"";position:absolute;left:-10px;top:26px;
  border-top:10px solid transparent;border-bottom:10px solid transparent;
  border-right:10px solid var(--grey-text);
}
.install-icon{position:absolute;left:22px;width:72px;height:56px;border-radius:4px;background:linear-gradient(135deg,#f1f1f1,#cfcfcf)}
.photo{background:linear-gradient(160deg,var(--wood) 0%,var(--wood-dark) 100%)}
.hero-photo{position:absolute;left:510px;top:90px;width:192px;height:108px;border-radius:6px}
.step{
  position:absolute;left:410px;width:364px;background:var(--card-navy);
  border-radius:8px;overflow:hidden;color:var(--white);
}
.step-photos{display:flex;gap:2px}
.step-photos .photo{flex:1}
.step-text{padding:4px 8px 0 8px;font-size:11.2px;line-height:1.15}
.info{
  position:absolute;left:802px;top:0;width:398px;height:848px;
  background:linear-gradient(180deg,var(--panel-blue) 0%,var(--panel-blue-deep) 100%);
  color:var(--white);
}
.info .banner{left:60px;width:280px}
.info-text{position:absolute;left:16px;width:366px;font-size:10.3px;line-height:15.4px;font-weight:300}
.info-text p{margin-bottom:15.4px}
.info-text .tight{margin-bottom:0}
.spec{position:absolute;left:16px;top:740px;font-size:13px;line-height:20.8px;font-weight:300}
</style>
</head>
<body>
<div class="sheet">

  <div class="banner" style="left:48px;top:14px;width:296px">Name of Part</div>
  <div class="parts-panel">
    <div class="parts-drawing" role="img" aria-label="Exploded technical drawing of the shower head parts"></div>
    <div class="part-label" style="left:46px;top:38px">G. White O-ring</div>
    <div class="part-label" style="left:30px;top:51px">H. Watering plate</div>
    <div class="part-label" style="left:22px;top:78px">I. Shower head cap</div>
    <div class="part-label" style="left:248px;top:37px">A. Shower head</div>
    <div class="part-label" style="left:258px;top:78px">B. Top O-ring</div>
    <div class="part-label" style="left:254px;top:104px">C. Water filter</div>
    <div class="part-label" style="left:142px;top:158px">J. Drill-free<br>bracket</div>
    <div class="part-label" style="left:244px;top:157px">D. Ceramic filter</div>
    <div class="part-label" style="left:134px;top:220px">K. Flexible hose</div>
    <div class="part-label" style="left:10px;top:253px">L. Water saver<br>&nbsp;&nbsp;(Pre-fitted<br>&nbsp;&nbsp;inside hose)</div>
    <div class="part-label" style="left:256px;top:270px">E. Handle</div>
    <div class="part-label" style="left:248px;top:348px">F. Bottom O-ring</div>
  </div>

  <div class="banner" style="left:48px;top:438px;width:304px">Installation</div>
  <div class="install-panel">
    <div class="install-icons">
      <div class="install-icon" role="img" aria-label="Removing old shower head" style="top:8px"></div>
      <div class="install-icon" role="img" aria-label="Fitting bracket to outlet" style="top:79px"></div>
      <div class="install-icon" role="img" aria-label="Vertical bracket alignment" style="top:150px"></div>
      <div class="install-icon" role="img" aria-label="Connecting the hose" style="top:221px"></div>
      <div class="install-icon" role="img" aria-label="Adjusting the bracket angle" style="top:292px"></div>
    </div>
    <div class="install-row" style="top:0">Remove the existing shower head by turning it anti-clockwise</div>
    <div class="install-row" style="top:71px">Fit the drill-free bracket clockwise to the shower head outlet. Tighten by hand only</div>
    <div class="install-row" style="top:142px">Ensure that the bracket is vertical and that the thread faces straight down</div>
    <div class="install-row" style="top:213px">Connect the hose to the shower head and to the bracket. The nut side of the hose should connect to the bracket. Make sure washers are placed inside the hose. Tighten by hand only</div>
    <div class="install-row" style="top:284px">To adjust the position of the bracket holder, place the shower head onto the bracket and use it as a lever to swivel the holder up and down.</div>
  </div>

  <div class="banner banner-assembly">Shower Head Assembly Instructions</div>
  <div class="hero-photo photo" role="img" aria-label="Photo of all shower head components laid out on a table"></div>

  <div class="step" style="top:214px;height:125px">
    <div class="step-photos" style="height:84px"><div class="photo" role="img" aria-label="Ceramic filter beside handle"></div><div class="photo" role="img" aria-label="Ceramic filter inside handle"></div></div>
    <div class="step-text">1. Insert (D) Ceramic filter into (E) Handle. Make sure the propeller side of the Ceramic filter goes into the Handle first, facing downwards.</div>
  </div>
  <div class="step" style="top:353px;height:125px">
    <div class="step-photos" style="height:83px"><div class="photo" role="img" aria-label="Water filter beside handle"></div><div class="photo" role="img" aria-label="Water filter inserted into handle"></div></div>
    <div class="step-text">2. Insert (C) Water filter into (E) Handle. Make sure the fat end of the Water filter goes into the Handle first, facing downwards.</div>
  </div>
  <div class="step" style="top:492px;height:166px">
    <div class="step-photos" style="height:84px"><div class="photo" role="img" aria-label="Watering plate placed in shower head cap"></div><div class="photo" role="img" aria-label="White O-ring placed on watering plate"></div></div>
    <div class="step-text">3. Place (H) Watering plate in the (I) Shower head cap. Make sure the side of the Watering plate with the engravings faces outwards (facing down on the table as in picture). Place the (G) White O-ring inside onto the Watering plate. Make sure the fat side of the White O-ring faces the Watering plate.</div>
  </div>
  <div class="step" style="top:673px;height:161px">
    <div class="step-photos" style="height:93px"><div class="photo" role="img" aria-label="Shower head screwed onto handle with cap beside"></div><div class="photo" role="img" aria-label="Fully assembled shower head"></div></div>
    <div class="step-text">4. Screw (A) Shower head onto the (E) Handle. Screw (I) Shower head cap onto the Shower head. Make sure the (B) Top O-ring and (F) Bottom O-ring are in the place properly. Missing or damaged O-rings may cause leaks.</div>
  </div>

  <aside class="info">
    <div class="banner" style="top:14px">Maintenance</div>
    <div class="info-text" style="top:64px">
      <p>It is recommended that you regularly clean your shower head to prevent blockage and/or damages. Regular maintenance will also ensure optimal water pressure level. The frequency of your maintenance routine should vary depending on the quality of water in your location.</p>
      <p>Because the photo-etched holes are very fine, lack of maintenance can cause build-up of lime, calcium and other particles in the holes. This can cause water pressure to exceed product specifications, leading to failures such as cracked parts, leaks, buckled shower plate, etc.</p>
      <p>To correctly maintain your product, simply disassemble the shower head and follow the instructions below.</p>
      <p class="tight">1. The ceramic filter is semi-permanent and will not need replacement if maintained correctly and if it is not damaged physically. Wash the ceramic filter under warm water and give it a good shake while rinsing to remove any build-up of dirt and other contaminants.</p>
      <p class="tight">2. To clean the watering plate:</p>
      <p class="tight">&nbsp;&nbsp;- Soak the watering plate in a bowl filled with white vinegar or fresh Fizzo cola</p>
      <p class="tight">&nbsp;&nbsp;- Cover the bowl with plastic wrap</p>
      <p class="tight">&nbsp;&nbsp;- Leave if for several hours, or overnight or longer if build-up is severe</p>
      <p class="tight">&nbsp;&nbsp;- Minerals, lime, calcium and other build-ups will dissolve away from the holes</p>
      <p class="tight">&nbsp;&nbsp;- Rinse the watering plate with cold water</p>
      <p class="tight">3. Wash other parts of the shower head and assemble back together, making sure all the components are placed correctly. (See “Assembly Instructions” for detailed information)</p>
      <p class="tight">4. The water filter can be replaced when dirty, or when the water pressure drops remarkably. Replacement cycles should vary depending on the amount of water consumed, water pressure, quality of the water in your location, etc. Average replacement cycle is once every 3 months.</p>
    </div>
    <div class="banner" style="top:500px">Important</div>
    <div class="info-text" style="top:546px">
      <p class="tight">Please read the manual before use, and follow the maintenance guidelines regularly to avoid possible damages or failures</p>
      <p class="tight">Do not soak the shower head in water for a long time.</p>
      <p class="tight">Do not use this product with hot water over 70°C.</p>
      <p class="tight">Some metal pieces may have sharp edges. Please exercise care when assembling.</p>
      <p class="tight">Gravity Fed users or users with under 100kpa water pressure in the region may not see improvements in their water pressure and/or may see fluctuations in the water temperature. Users with instantaneous hot water system may also see fluctuations in their water temperature.</p>
    </div>
    <div class="banner" style="top:692px">Specification</div>
    <div class="spec">
      <div>Materials: Heat-resistant PC</div>
      <div>Recommended temperature: 0 ~ 70</div>
      <div>Watering plate holes: Ø 0.20 / 412EA</div>
      <div>Made in Korea</div>
    </div>
  </aside>

</div>
</body>
</html>
```